Quill Physical Therapy Website

I would need a clean modern website built to showcase my Physical therapy brand and services. I would need a simple but descriptive website that can ultimately connect my patients to my electronic medical portal so they may book an appointment..

```html
<!DOCTYPE html>
<html lang="en">
<head>
<meta charset="utf-8">
<title>Quill Physical Therapy</title>
<link href="https://fonts.googleapis.com/css2?family=Lato:ital,wght@0,400;0,700;0,900;1,400&display=swap" rel="stylesheet">
<style>
:root{
  --indigo:#3a45a0;
  --teal:#1e7a6e;
  --teal-dark:#17695e;
  --green:#6cbf45;
  --ink:#3a3a3a;
  --muted:#555;
  --light:#f1f1f1;
  --white:#fff;
  --footer-base:#1b3f3c;
}
*{margin:0;padding:0;box-sizing:border-box}
html,body{width:1200px;height:4403px;overflow:hidden}
body{font-family:'Lato',sans-serif;color:var(--ink);background:var(--white);position:relative}
.abs{position:absolute}
.btn{display:inline-block;background:var(--green);color:var(--white);font-weight:700;font-size:16px;text-transform:uppercase;text-align:center;letter-spacing:.3px}
.photo{position:absolute}

/* top bar + nav */
.topbar{left:0;top:0;width:1200px;height:58px;background:var(--indigo);color:var(--white);font-size:16px;font-weight:700}
.topbar .contact{position:absolute;right:74px;top:18px;display:flex;gap:36px;align-items:center}
.topbar .contact span{display:flex;gap:10px;align-items:center}
.nav{left:0;top:58px;width:1200px;height:89px;background:var(--white)}
.nav ul{list-style:none;position:absolute;right:74px;top:37px;display:flex;gap:31px;font-size:14px;font-weight:700;color:#222}
.nav li.active{color:var(--teal)}
.brand{left:75px;top:0;width:205px;height:216px;background:var(--white);z-index:3;display:flex;flex-direction:column;align-items:center;justify-content:center;gap:14px}
.brand .dot{width:70px;height:70px;border-radius:50%;background:var(--teal)}
.brand .name{font-size:25px;font-weight:900;color:var(--teal);text-align:center;line-height:1.1}

/* hero */
.hero{left:0;top:147px;width:1200px;height:705px;background:linear-gradient(110deg,#8a8f92 0%,#c7c3bd 40%,#9b8574 65%,#d9dde2 100%)}
.hero h1{position:absolute;left:0;top:230px;width:1200px;text-align:center;color:var(--white);font-weight:900;text-transform:uppercase;line-height:1.1}
.hero h1 .l1{display:block;font-size:64px}
.hero h1 .l2{display:block;font-size:70px}
.hero .btn{position:absolute;left:470px;top:413px;width:260px;height:50px;line-height:50px;font-size:17px}

.features{left:75px;top:786px;width:1034px;height:226px;display:flex}
.feature{flex:1;position:relative;color:var(--white);text-align:center}
.feature.f1{background:var(--teal)}.feature.f2{background:var(--green)}.feature.f3{background:var(--indigo)}
.feature .icon{position:absolute;left:50%;top:-56px;margin-left:-58px;width:116px;height:116px;border-radius:50%;border:5px solid var(--white);display:flex;align-items:center;justify-content:center}
.f1 .icon{background:var(--teal)}.f2 .icon{background:var(--green)}.f3 .icon{background:var(--indigo)}
.feature h3{position:absolute;top:80px;width:100%;font-size:27px;font-weight:900;line-height:1.15;text-transform:uppercase}
.feature .outline{position:absolute;left:50%;margin-left:-63px;top:160px;width:126px;height:34px;line-height:30px;border:2px solid var(--white);font-size:13px;font-weight:700}

/* about */
.about{left:0;top:1092px;width:1200px;height:483px;background:#f2f4f4}
.about .pic{left:647px;top:0;width:553px;height:483px;background:linear-gradient(120deg,#e8e8e6,#c9b8a8 50%,#efefef)}
.about .mark{left:302px;top:80px;width:44px;height:44px;border-radius:50%;background:var(--teal)}
.about h2{position:absolute;left:40px;top:150px;width:570px;text-align:center;font-size:29px;font-weight:900;color:var(--teal);text-transform:uppercase;white-space:nowrap}
.about p{position:absolute;left:80px;top:196px;width:485px;text-align:center;font-size:16px;line-height:28px;color:var(--muted)}
.about .btn{position:absolute;left:242px;top:357px;width:164px;height:50px;line-height:50px}

/* section headings */
.sec-title{position:absolute;left:0;width:1200px;text-align:center;font-size:30px;font-weight:900;text-transform:uppercase}
.sec-title.teal{color:var(--teal)}
.sec-mark{position:absolute;left:578px;width:44px;height:44px;border-radius:50%;background:var(--teal)}

/* cards */
.card{position:absolute;width:330px;background:var(--light);text-align:center}
.card .thumb{width:330px;height:203px}
.card h4{font-size:18px;font-weight:900;color:var(--indigo);text-transform:uppercase;line-height:26px}
.card p{font-size:14px;line-height:24px;color:var(--muted);padding:0 22px}
.card .btn{position:absolute;left:82px;width:166px;height:52px;line-height:52px}
.service{top:1757px;height:477px}
.service h4{margin-top:22px}.service p{margin-top:8px}.service .btn{top:390px}
.blog{top:3533px;height:474px;background:var(--white)}
.blog h4{margin-top:20px}.blog p{margin-top:6px}.blog .btn{top:392px}

/* testimonials */
.testimonials{left:0;top:2275px;width:1200px;height:470px;background:linear-gradient(100deg,#1e7a6e 0%,#2a5b8e 55%,#3a45a0 100%);color:var(--white);text-align:center}
.testimonials .ring{left:1000px;top:40px;width:210px;height:210px;border-radius:50%;border:18px solid rgba(255,255,255,.07)}
.testimonials h2{position:absolute;top:55px;width:100%;font-size:30px;font-weight:900}
.testimonials blockquote{position:absolute;left:145px;top:110px;width:910px;font-size:18px;font-style:italic;line-height:29px}
.testimonials .arrow{position:absolute;top:200px}
.testimonials .avatar{position:absolute;left:550px;top:240px;width:90px;height:90px;border-radius:50%;background:linear-gradient(#f1b31c,#e79b14)}
.testimonials .quote{position:absolute;left:622px;top:286px;font-size:72px;font-weight:900;color:var(--green);line-height:60px}
.testimonials .who{position:absolute;top:353px;width:100%;font-size:16px;font-weight:700}
.testimonials .loc{position:absolute;top:377px;width:100%;font-size:14px;opacity:.85}

/* gallery */
.gallery .photo{width:330px;height:229px}

/* blog section */
.blog-bg{left:0;top:3420px;width:1200px;height:616px;background:var(--light)}

/* footer */
.footer{left:0;top:4036px;width:1200px;height:291px;background:var(--teal-dark);color:var(--white)}
.footer .fbrand{position:absolute;left:95px;top:60px;width:180px;display:flex;flex-direction:column;align-items:center;gap:14px}
.footer .fbrand .dot{width:70px;height:70px;border-radius:50%;background:var(--white)}
.footer .fbrand .name{font-size:24px;font-weight:900;text-align:center;line-height:1.1}
.footer h5{position:absolute;top:60px;font-size:16px;font-weight:900;text-transform:uppercase}
.footer .links{position:absolute;left:355px;top:95px;display:grid;grid-template-columns:122px 100px;row-gap:12px;font-size:14px}
.footer .info{position:absolute;left:614px;top:95px;font-size:14px;line-height:20px;width:210px}
.footer .info div{display:flex;gap:14px;margin-bottom:14px}
.footer .info svg{flex:none;margin-top:2px}
.footer input{position:absolute;left:884px;width:242px;height:42px;border:none;padding-left:14px;font-family:'Lato',sans-serif;font-size:13px;color:#333}
.footer .btn{position:absolute;left:1038px;top:216px;width:88px;height:40px;line-height:40px;font-size:15px}
.bottombar{left:0;top:4327px;width:1200px;height:76px;background:var(--footer-base);color:var(--white)}
.bottombar .copy{position:absolute;left:75px;top:30px;font-size:13px}
.bottombar .social{position:absolute;right:74px;top:26px;display:flex;gap:16px}
.bottombar .social span{width:22px;height:22px;border-radius:50%;background:var(--white)}
</style>
</head>
<body>

<div class="abs topbar">
  <div class="contact">
    <span><svg width="16" height="16" viewBox="0 0 24 24" fill="#fff"><path d="M6.6 10.8a15 15 0 006.6 6.6l2.2-2.2c.3-.3.7-.4 1-.2 1.1.4 2.3.6 3.6.6.6 0 1 .4 1 1V20c0 .6-.4 1-1 1A17 17 0 013 4c0-.6.4-1 1-1h3.5c.6 0 1 .4 1 1 0 1.3.2 2.5.6 3.6.1.3 0 .7-.2 1z"/></svg>1-800-555-0142</span>
    <span><svg width="16" height="14" viewBox="0 0 24 20" fill="#fff"><path d="M0 2l12 8 12-8V0H0zM0 5v15h24V5l-12 8z"/></svg>hello@quillpt.example</span>
  </div>
</div>

<nav class="abs nav">
  <ul>
    <li class="active">HOME</li><li>ABOUT US</li><li>SERVICES</li><li>TESTIMONIALS</li><li>BLOG</li><li>CAREER</li><li>CONTACT US</li>
  </ul>
</nav>

<div class="abs brand">
  <div class="dot"></div>
  <div class="name">QUILL PHYSICAL THERAPY</div>
</div>

<section class="abs hero">
  <div class="photo" role="img" aria-label="Physical therapist working on a patient's shoulder" style="inset:0;background:inherit"></div>
  <h1><span class="l1">Welcome to</span><span class="l2">Quill Physical Therapy</span></h1>
  <span class="btn">Book an Appointment</span>
</section>

<div class="abs features">
  <div class="feature f1">
    <div class="icon"><svg width="52" height="52" viewBox="0 0 52 52" fill="#fff"><circle cx="26" cy="10" r="7"/><rect x="6" y="30" width="40" height="6" rx="2"/><rect x="12" y="38" width="4" height="10"/><rect x="36" y="38" width="4" height="10"/><rect x="18" y="20" width="16" height="8" rx="3"/></svg></div>
    <h3>Our<br>Services</h3><span class="outline">VIEW SERVICES</span>
  </div>
  <div class="feature f2">
    <div class="icon"><svg width="56" height="52" viewBox="0 0 56 52" fill="#fff"><circle cx="28" cy="12" r="8"/><circle cx="12" cy="20" r="6"/><circle cx="44" cy="20" r="6"/><path d="M14 48c0-10 6-18 14-18s14 8 14 18z"/><path d="M2 46c0-8 4-14 10-14 3 0 5 1 6 3-3 3-5 7-5 11z"/><path d="M54 46c0-8-4-14-10-14-3 0-5 1-6 3 3 3 5 7 5 11z"/></svg></div>
    <h3>Expert<br>Team</h3><span class="outline">VIEW TEAM</span>
  </div>
  <div class="feature f3">
    <div class="icon"><svg width="50" height="50" viewBox="0 0 50 50" fill="none" stroke="#fff" stroke-width="3"><rect x="4" y="8" width="42" height="38" rx="3"/><line x1="4" y1="18" x2="46" y2="18"/><line x1="14" y1="3" x2="14" y2="12"/><line x1="36" y1="3" x2="36" y2="12"/><g fill="#fff" stroke="none"><rect x="11" y="23" width="6" height="5"/><rect x="22" y="23" width="6" height="5"/><rect x="33" y="23" width="6" height="5"/><rect x="11" y="33" width="6" height="5"/><rect x="22" y="33" width="6" height="5"/><rect x="33" y="33" width="6" height="5"/></g></svg></div>
    <h3>Get Easy<br>Appointment</h3><span class="outline">BOOK NOW</span>
  </div>
</div>

<section class="abs about">
  <div class="photo pic" role="img" aria-label="Therapist guiding a woman through an arm stretch"></div>
  <div class="photo mark"></div>
  <h2>About Quill Physical Therapy</h2>
  <p>Nunc sollicitudin congue lacus ut vestibulumdonec at varius augue. Sed efficitur venenatis tellus, non dictum quam venenatis sit amet. Nulla turpis mi, vulputate et diam quis, pharetra posuere justo placerat dolor a risus euismod, sed tempor elit porta.</p>
  <span class="btn">Read More</span>
</section>

<div class="sec-mark" style="top:1622px"></div>
<h2 class="sec-title teal" style="top:1694px">Our Services</h2>

<div class="card service" style="left:75px">
  <div class="thumb" role="img" aria-label="Therapist stretching a patient's leg on a treatment table" style="background:linear-gradient(135deg,#cfe3ef,#4a7fa8)"></div>
  <h4>Services Heading</h4>
  <p>Nunc sollicitudin congue lacus ut vestibulumdonec at variu non dictum quam venenatis sit amet. Nulla turpis mi, vulputate et diam quis.</p>
  <span class="btn">Read More</span>
</div>
<div class="card service" style="left:434px">
  <div class="thumb" role="img" aria-label="Hands treating a patient's lower back" style="background:linear-gradient(135deg,#e7d2c6,#d56b5a 55%,#e9ddd6)"></div>
  <h4>Services Heading</h4>
  <p>Nunc sollicitudin congue lacus ut vestibulumdonec at variu non dictum quam venenatis sit amet. Nulla turpis mi, vulputate et diam quis.</p>
  <span class="btn">Read More</span>
</div>
<div class="card service" style="left:794px">
  <div class="thumb" role="img" aria-label="Therapist treating a patient lying on a clinic bed" style="background:linear-gradient(135deg,#eeeae4,#c9b7a5 60%,#6f6a64)"></div>
  <h4>Services Heading</h4>
  <p>Nunc sollicitudin congue lacus ut vestibulumdonec at variu non dictum quam venenatis sit amet. Nulla turpis mi, vulputate et diam quis.</p>
  <span class="btn">Read More</span>
</div>

<section class="abs testimonials">
  <div class="abs ring"></div>
  <h2>TESTIMONIALS</h2>
  <blockquote>"Sed ut perspiciatis unde omnis iste natus error sit voluptatem accusantium doloremque laudantium, totam rem aperiam, eaque ipsa quae ab illo inventore veritatis et quasi architecto beatae vitae dicta sunt explicabo. Nemo enim ipsam voluptatem quia voluptas sit aspernatur aut odit aut fugit, sed quia consequuntur magni dolores eos qui ratione voluptatem sequi nesciunt..."</blockquote>
  <svg class="arrow" style="left:62px" width="16" height="30" viewBox="0 0 16 30" fill="none" stroke="#fff" stroke-width="2.5"><path d="M14 2L2 15l12 13"/></svg>
  <svg class="arrow" style="left:1122px" width="16" height="30" viewBox="0 0 16 30" fill="none" stroke="#fff" stroke-width="2.5"><path d="M2 2l12 13L2 28"/></svg>
  <div class="avatar" role="img" aria-label="Portrait of the reviewing patient"></div>
  <div class="quote">”</div>
  <div class="who">MARCUS REED</div>
  <div class="loc">Location</div>
</section>

<h2 class="sec-title teal" style="top:2802px">Gallery</h2>
<div class="gallery">
  <div class="photo" style="left:75px;top:2870px;background:linear-gradient(135deg,#3c6ea8,#a8b5bf 60%,#222)" role="img" aria-label="Therapist flexing a patient's knee"></div>
  <div class="photo" style="left:434px;top:2870px;background:linear-gradient(135deg,#eef0ef,#c9cdd0 60%,#2d4f86)" role="img" aria-label="Older man stretching his arm with a therapist"></div>
  <div class="photo" style="left:794px;top:2870px;background:linear-gradient(135deg,#8d8a86,#4a5a70 60%,#cfc8bf)" role="img" aria-label="Group of smiling clinic staff"></div>
  <div class="photo" style="left:75px;top:3131px;background:linear-gradient(135deg,#d9d0c4,#f2efea 50%,#b7a898)" role="img" aria-label="Therapist massaging a woman on a table"></div>
  <div class="photo" style="left:434px;top:3131px;background:linear-gradient(135deg,#dfe4ea,#b5bcc4 55%,#f0f0f0)" role="img" aria-label="Older man lifting dumbbells with a therapist"></div>
  <div class="photo" style="left:794px;top:3131px;background:linear-gradient(135deg,#d7e6ee,#c94a3e 40%,#d9e4ea)" role="img" aria-label="Patient walking between parallel bars"></div>
</div>

<div class="abs blog-bg"></div>
<h2 class="sec-title teal" style="top:3473px">Blog Posts</h2>

<div class="card blog" style="left:75px">
  <div class="thumb" role="img" aria-label="Man with shoulder pain being examined" style="background:linear-gradient(135deg,#efefef,#b4463f 50%,#d8d2cc)"></div>
  <h4>Neque porro quisquam<br>est qui dolorem</h4>
  <p>Nunc sollicitudin congue lacus ut vestibulumdonec at variu non dictum quam venenatis sit amet.</p>
  <span class="btn">Read More</span>
</div>
<div class="card blog" style="left:434px">
  <div class="thumb" role="img" aria-label="Woman exercising with a therapist in a gym" style="background:linear-gradient(135deg,#e8edf0,#8a9aa6 55%,#2d4f86)"></div>
  <h4>Neque porro quisquam<br>est qui dolorem</h4>
  <p>Nunc sollicitudin congue lacus ut vestibulumdonec at variu non dictum quam venenatis sit amet.</p>
  <span class="btn">Read More</span>
</div>
<div class="card blog" style="left:794px">
  <div class="thumb" role="img" aria-label="Patient training on an exercise ball in a rehab gym" style="background:linear-gradient(135deg,#d9c3a8,#4a9a55 55%,#c9b8a6)"></div>
  <h4>Neque porro quisquam<br>est qui dolorem</h4>
  <p>Nunc sollicitudin congue lacus ut vestibulumdonec at variu non dictum quam venenatis sit amet.</p>
  <span class="btn">Read More</span>
</div>

<footer class="abs footer">
  <div class="fbrand"><div class="dot"></div><div class="name">QUILL PHYSICAL THERAPY</div></div>
  <h5 style="left:355px">Site Map</h5>
  <div class="links"><span>Home</span><span>Blog</span><span>About Us</span><span>Career</span><span>Services</span><span>Contact Us</span><span>Testimonials</span></div>
  <h5 style="left:614px">Contact Info</h5>
  <div class="info">
    <div><svg width="12" height="16" viewBox="0 0 12 16" fill="#fff"><path d="M6 0a6 6 0 00-6 6c0 4.5 6 10 6 10s6-5.5 6-10a6 6 0 00-6-6zm0 8.5A2.5 2.5 0 116 3.5a2.5 2.5 0 010 5z"/></svg><span>Nemo enim ipsam volup tatem quia volupta</span></div>
    <div><svg width="14" height="14" viewBox="0 0 24 24" fill="#fff"><path d="M6.6 10.8a15 15 0 006.6 6.6l2.2-2.2c.3-.3.7-.4 1-.2 1.1.4 2.3.6 3.6.6.6 0 1 .4 1 1V20c0 .6-.4 1-1 1A17 17 0 013 4c0-.6.4-1 1-1h3.5c.6 0 1 .4 1 1 0 1.3.2 2.5.6 3.6.1.3 0 .7-.2 1z"/></svg><span>1-800-555-0142</span></div>
    <div><svg width="14" height="12" viewBox="0 0 24 20" fill="#fff"><path d="M0 2l12 8 12-8V0H0zM0 5v15h24V5l-12 8z"/></svg><span>hello@quillpt.example</span></div>
    <div style="font-weight:700">Map Direction</div>
  </div>
  <h5 style="left:884px">Email Sign Up</h5>
  <input style="top:96px" placeholder="Enter Name">
  <input style="top:150px" placeholder="Enter Email Address">
  <span class="btn">Sign Up</span>
</footer>

<div class="abs bottombar">
  <div class="copy">Copyright © 2021. Company Name All Right Reserved</div>
  <div class="social"><span></span><span></span><span></span><span></span><span></span><span></span></div>
</div>

</body>
</html>
```